The Brindlecove Disinfecting Services

I need a logo that I will be able to send to printing company to make a magnet banner for my work vans. It should have my company name on it as well as website and phone number. Also a graphic of an electrostatic gun spraying schools. We provide electrostatic disinfecting for businesses so this would be perfect.
Thank you
Hvala

```html
<!DOCTYPE html>
<html lang="en">
<head>
<meta charset="utf-8">
<title>The Brindlecove Disinfecting Services – Van Magnet</title>
<link rel="stylesheet" href="https://fonts.googleapis.com/css2?family=Syncopate:wght@400;700&family=Questrial&display=swap">
<style>
  :root {
    --page: #e9e9e7;
    --sign: #ffffff;
    --ink: #1f1f1f;
    --brand-green: #4b7a47;
    --on-green: #ffffff;
  }
  html, body {
    margin: 0;
    width: 1030px;
    height: 1200px;
    overflow: hidden;
    background: var(--page);
  }
  .magnet-sign {
    position: absolute;
    left: 20px;
    top: 313px;
    width: 990px;
    height: 577px;
    background: var(--sign);
    box-shadow: 0 2px 6px rgba(0,0,0,0.15);
  }
  .magnet-sign svg { display: block; width: 100%; height: 100%; }
  .company-name { font-family: "Syncopate", "Arial Black", sans-serif; font-weight: 400; fill: var(--ink); }
  .service-line { font-family: "Syncopate", "Arial Black", sans-serif; font-weight: 700; fill: var(--on-green); }
  .phone-number, .web-address { font-family: "Questrial", "Century Gothic", sans-serif; fill: var(--ink); }
  .service-band { fill: var(--brand-green); }
</style>
</head>
<body>
  <div class="magnet-sign">
    <svg viewBox="0 0 1035 603" xmlns="http://www.w3.org/2000/svg">
      <defs>
        <linearGradient id="desk-tone" x1="0" y1="0" x2="0" y2="1">
          <stop offset="0" stop-color="#f5b264"/>
          <stop offset="1" stop-color="#e9c9b2"/>
        </linearGradient>
        <linearGradient id="mist-tone" x1="1" y1="0" x2="0" y2="0">
          <stop offset="0" stop-color="#ee6a3c" stop-opacity="0.85"/>
          <stop offset="1" stop-color="#ee6a3c" stop-opacity="0.15"/>
        </linearGradient>
        <linearGradient id="sprayer-tone" x1="0" y1="0" x2="1" y2="1">
          <stop offset="0" stop-color="#2e7a34"/>
          <stop offset="0.6" stop-color="#e9eef0"/>
          <stop offset="1" stop-color="#5d8fc9"/>
        </linearGradient>
      </defs>

      <text class="company-name" x="35" y="88" textLength="965" lengthAdjust="spacingAndGlyphs"><tspan font-size="84">T</tspan><tspan font-size="66">HE </tspan><tspan font-size="84">B</tspan><tspan font-size="66">RINDLECOVE</tspan></text>

      <rect class="service-band" x="0" y="115" width="1035" height="72"/>
      <text class="service-line" x="35" y="167" font-size="44" textLength="962" lengthAdjust="spacingAndGlyphs">DISINFECTING SERVICES</text>

      <rect class="school-desk-art" role="img" aria-label="Illustration of a wooden school desk chair covered in disinfectant droplets"
            x="47" y="215" width="240" height="300" rx="6" fill="url(#desk-tone)"/>
      <rect class="spray-mist-art" role="img" aria-label="Cone of orange charged disinfectant droplets spraying toward the desk"
            x="300" y="222" width="356" height="136" rx="68" fill="url(#mist-tone)"/>
      <rect class="sprayer-art" role="img" aria-label="Photo of a gloved hand holding a green electrostatic disinfecting sprayer"
            x="672" y="250" width="345" height="175" rx="6" fill="url(#sprayer-tone)"/>

      <text class="phone-number" x="307" y="510" font-size="80" textLength="680" lengthAdjust="spacingAndGlyphs">555-013-2847</text>
      <text class="web-address" x="52" y="585" font-size="50" textLength="935" lengthAdjust="spacingAndGlyphs">WWW.BRINDLECOVETCB.COM</text>
    </svg>
  </div>
</body>
</html>
```